Podcast Cover Art for rebranded podcast - I have inspiration for the designs

I've had a podcast ("Paperboat Radio Hour") since 2018, but I'm in the process of rebranding it. I've attached the old cover art below, which I loved, but I don't need it to look like that at all. The rebranded podcast is called 'Open Window with Marnie Cole.' I've included the show description at the bottom. I've been working on various design options in Canva, but not obsessed with anything yet, but I'm attaching the ones I do like that I think just need some refining. My very favorite is the one labeled 'favorite_Open Window' so I wouldn't mind keeping that general idea but perfected by a designer. Ultimately, I want something cool, fairly clean, modern, eye catching. I'm into neutrals with maybe a pop of color, so think black, white, grey..maybe silver, and I love a pop of red..and I'm not opposed to other options for the pop color. The show is going to be inspiring, entertaining, and funny. Oh and one other idea I had but I'm not sure if it makes sense with the title and/or what the show is about..but a vinyl record with Open Window with Marnie Cole on it somehow, on a record player..not sure.

Ever wonder what it means to truly live authentically? Curious about how to embrace the unpredictability of life? Ready for some heartfelt and lighthearted conversations that inspire and entertain?
Join Marnie Cole as she dives into the raw, real, and unscripted moments of life. In each episode, Marnie brings candid conversations and genuine insights into the ups and downs we all experience. From personal growth and self-discovery to inspiring stories and valuable life lessons, "Open Window" is a space where authenticity reigns and spontaneity is celebrated.
Whether she's sharing her own journey or chatting with inspiring guests, Marnie invites you to explore the beauty of living life without a script. Expect honest reflections, thought-provoking discussions, and a refreshing perspective on navigating life's unpredictable path—all with a dash of fun and humor to keep things lively and entertaining. Step into the unscripted moments of life and tune in for a blend of depth and lightheartedness that will leave you inspired, smiling, and most importantly laughing.

Target Market(s)

25-50 year old women and men (primarily women)

Font styles to use
Sans Serif

Requirements
Should not have
• nothing too feminine or girly, nothing cheesy :)

```html
<!DOCTYPE html>
<html lang="en">
<head>
<meta charset="utf-8">
<title>Open Window with Marnie Cole – Podcast Cover</title>
<link rel="stylesheet" href="https://fonts.googleapis.com/css2?family=Bebas+Neue&family=Kaushan+Script&family=Montserrat:wght@500&display=swap">
<style>
  :root {
    --stage: #cbcbcb;
    --ink: #051a22;
    --ink-soft: #0d2731;
    --red: #e0153e;
    --pink: #e8455f;
    --white: #ffffff;
  }
  * { margin: 0; padding: 0; box-sizing: border-box; }
  html, body {
    width: 1200px; height: 1033px; overflow: hidden;
    background: var(--stage);
  }
  .cover {
    position: absolute; left: 110px; top: 26px;
    width: 980px; height: 980px;
    background: var(--ink);
    overflow: hidden;
  }
  .host-backdrop {
    position: absolute; right: 0; top: 0;
    width: 360px; height: 980px;
    background: radial-gradient(ellipse at 55% 30%, rgba(40,70,80,0.55), rgba(5,26,34,0) 70%);
  }
  .show-title {
    position: absolute; left: 0; right: 0; top: 70px;
    display: flex; justify-content: center; align-items: center; gap: 22px;
  }
  .show-title .script {
    font-family: "Kaushan Script", cursive;
    color: var(--red);
    font-size: 130px; line-height: 1;
    transform: rotate(-4deg);
  }
  .show-title .block {
    font-family: "Bebas Neue", sans-serif;
    color: var(--white);
    font-size: 158px; line-height: 1; letter-spacing: 2px;
    padding-top: 14px;
  }
  .photo { position: absolute; width: 171px; }
  .photo--mirror { left: 122px; top: 352px; height: 351px;
    background: linear-gradient(180deg, #6d7a5c 0%, #c0303a 35%, #b62b35 60%, #2a2622 100%); }
  .photo--desk { left: 310px; top: 299px; height: 475px;
    background: linear-gradient(160deg, #c81c3f 0%, var(--pink) 55%, #ef6b82 100%); }
  .photo--dance { left: 498px; top: 232px; height: 518px;
    background: linear-gradient(180deg, #c9c9c9 0%, #6d6d6d 40%, #2b2b2b 75%, #8a8a8a 100%); }
  .photo--seated { left: 684px; top: 312px; height: 478px;
    background: linear-gradient(170deg, var(--red) 0%, #b5102f 55%, #e0284c 100%); }
  .byline {
    position: absolute; left: 0; right: 0; top: 830px;
    display: flex; justify-content: center; align-items: baseline; gap: 26px;
  }
  .byline .with {
    font-family: "Montserrat", sans-serif; font-weight: 500;
    color: var(--white); font-size: 42px;
  }
  .byline .host {
    font-family: "Kaushan Script", cursive;
    color: var(--red); font-size: 76px; line-height: 1;
  }
</style>
</head>
<body>
  <main class="cover">
    <div class="host-backdrop" role="img" aria-label="Faint dark-toned portrait of the host smiling, fading into the background"></div>

    <h1 class="show-title">
      <span class="script">Open</span>
      <span class="block">WINDOW</span>
    </h1>

    <div class="photo photo--mirror" role="img" aria-label="Colour photo of the host in a red top laughing beside a mirror"></div>
    <div class="photo photo--desk" role="img" aria-label="Red-tinted photo of the host at a desk with laptop, phone and microphone"></div>
    <div class="photo photo--dance" role="img" aria-label="Black and white photo of the host dancing with an arm raised"></div>
    <div class="photo photo--seated" role="img" aria-label="Red-tinted photo of the host seated and smiling"></div>

    <p class="byline">
      <span class="with">with</span>
      <span class="host">Marnie Cole</span>
    </p>
  </main>
</body>
</html>
```